Bright Nook Home Page (A Home Wellness e-commerce site & blog)

We need a dynamic home page created for a home wellness brand. Must be visually appealing and extremely mobile-friendly. Logos and a Navmap have been provided but that is just a guideline, PLEASE USE YOUR CREATIVITY.

Target Market(s)

1st target demo: females 24-48, 2nd target demo: all 24-48

Number of Pages Required

1 page

```html
<!DOCTYPE html>
<html lang="en">
<head>
<meta charset="utf-8">
<title>Bright Nook – Home Wellness</title>
<link href="https://fonts.googleapis.com/css2?family=Poppins:wght@300;400;500;600;700&family=Lato:wght@400;700;900&display=swap" rel="stylesheet">
<style>
:root{
  --teal:#2fb5be;
  --purple:#4b1f87;
  --purple-deep:#3d1672;
  --ink:#1f1f24;
  --text:#3a3a3a;
  --muted:#6b6b6b;
  --footer:#1d1d1f;
  --white:#ffffff;
  --mist:#eef0f3;
}
*{margin:0;padding:0;box-sizing:border-box}
html,body{width:1200px;height:4104px;overflow:hidden;background:var(--white)}
body{position:relative;font-family:"Lato",sans-serif;color:var(--text)}
.abs{position:absolute}
a{color:inherit;text-decoration:none}

/* top strip + nav */
.promo-strip{left:0;top:0;width:1200px;height:30px;background:var(--teal);color:var(--white);font:600 13px/30px "Poppins",sans-serif;text-align:center}
.site-nav{left:0;top:30px;width:1200px;height:90px;background:var(--purple)}
.brand{font:500 36px/1 "Poppins",sans-serif;color:var(--white);letter-spacing:-.5px}
.site-nav .brand{left:116px;top:27px}
.nav-links{left:411px;top:0;height:90px;display:flex;gap:0;align-items:center;font:500 17px "Poppins",sans-serif;color:var(--white)}
.nav-links a{position:absolute;white-space:nowrap;top:34px}
.nav-links a.active{font-weight:700}
.social-ring{width:34px;height:34px;border:2px solid var(--white);border-radius:50%}
.cart-icon{left:1038px;top:58px}

/* hero */
.hero{left:0;top:120px;width:1200px;height:581px;background:linear-gradient(100deg,#f7f7f9 0%,#f1eff6 40%,#cfc1ea 60%,#a68dd6 75%,#c8a48a 90%,#efe9f3 100%)}
.hero-title{left:128px;top:128px;font:700 60px/1 "Poppins",sans-serif;color:var(--purple)}
.hero-title span{display:block;font-weight:400;margin-top:0}
.hero-copy{left:128px;top:260px;width:305px;font:400 16px/22px "Lato",sans-serif;color:var(--ink)}
.btn{display:block;background:var(--teal);color:var(--white);font:700 15px "Poppins",sans-serif;text-align:center;text-transform:uppercase;border-radius:2px}
.hero .btn{left:128px;top:366px;width:159px;height:45px;line-height:45px}
.slide-arrow{width:40px;height:40px;border:2px solid #888;border-radius:50%}

/* framed banners */
.framed-banner{background:linear-gradient(120deg,#6b44ae,#7e5bbd 45%,#6a46aa 70%,#5a36a0);text-align:center;color:var(--white)}
.framed-banner::after{content:"";position:absolute;inset:8px;border:2px solid rgba(255,255,255,.9)}
.sale-banner{left:145px;top:754px;width:913px;height:298px}
.sale-title{position:absolute;left:0;right:0;top:72px;font:700 40px "Poppins",sans-serif}
.sale-sub{position:absolute;left:0;right:0;top:126px;font:400 28px "Lato",sans-serif;letter-spacing:.5px}
.sale-banner .btn{position:absolute;left:389px;top:183px;width:132px;height:42px;line-height:42px;font-size:13px;font-weight:500;z-index:1}

/* section headings */
.section-head{left:0;width:1200px;text-align:center}
.section-head h2{font:700 40px "Poppins",sans-serif;color:var(--ink)}
.section-head .smile{display:block;margin:8px auto 0}
.section-head p{margin-top:18px;font:700 23px "Lato",sans-serif;color:var(--purple)}

/* featured grid */
.tile{overflow:hidden}
.info-card{color:var(--white);padding:44px 28px 0 28px}
.info-card h3{font:600 14px/21px "Poppins",sans-serif;text-transform:uppercase}
.info-card p{margin-top:10px;font:400 15px/22px "Lato",sans-serif;opacity:.92}
.info-card .more{display:block;margin-top:16px;font:700 12px "Poppins",sans-serif;letter-spacing:.3px}

/* about */
.about{left:0;top:2113px;width:1200px;height:593px;background:linear-gradient(120deg,#e3e6ea,#f4f5f7 40%,#eceef1 70%,#dfe2e6)}
.about h2{left:143px;top:80px;font:700 30px "Poppins",sans-serif;color:var(--ink)}
.about .smile{left:143px;top:132px}
.about p{left:143px;top:177px;width:420px;font:400 18px/25.6px "Lato",sans-serif;color:var(--ink)}
.about .btn{left:143px;top:386px;width:160px;height:45px;line-height:45px;font-size:14px;font-weight:500}

.pay-banner{left:143px;top:2649px;width:912px;height:298px;background:linear-gradient(100deg,#4a2291,#5c36a4 40%,#6a47ad 70%,#4f2a95)}
.pay-brand{position:absolute;left:0;right:0;top:74px;font:500 36px "Poppins",sans-serif;display:flex;justify-content:center;align-items:center;gap:12px}
.pay-brand i{width:30px;height:30px;border-radius:50%;background:var(--white)}
.pay-line1{position:absolute;left:0;right:0;top:140px;font:700 32px "Poppins",sans-serif}
.pay-line2{position:absolute;left:0;right:0;top:182px;font:700 38px "Poppins",sans-serif;letter-spacing:.5px}

/* blog */
.post{width:280px;height:406px}
.post .thumb{position:absolute;left:0;top:0;width:280px;height:228px}
.post .body{position:absolute;left:8px;top:191px;width:264px;height:215px;background:var(--white);border-bottom:3px solid var(--teal);box-shadow:0 2px 8px rgba(0,0,0,.12);padding:24px 20px 0 28px}
.post h3{font:600 17px/22px "Poppins",sans-serif;color:var(--ink)}
.post .date{margin-top:10px;font:700 14px "Poppins",sans-serif;color:var(--teal);display:flex;align-items:center;gap:6px}
.post p{margin-top:10px;font:400 14.5px/19px "Lato",sans-serif;color:var(--text)}
.post .more{display:block;margin-top:12px;font:700 12px "Poppins",sans-serif;color:var(--teal)}

.chat-bubble{left:1063px;top:3610px;width:100px;height:100px;border-radius:50%;background:var(--purple-deep);z-index:3;display:flex;align-items:center;justify-content:center}

/* footer */
.site-footer{left:0;top:3663px;width:1200px;height:441px;background:var(--footer);color:#d6d6d6}
.site-footer .brand{left:105px;top:64px}
.foot-social{width:32px;height:32px;border:2px solid #d6d6d6;border-radius:50%}
.foot-col h4{font:600 18px "Poppins",sans-serif;color:var(--white);letter-spacing:.3px}
.foot-col ul{list-style:none;margin-top:16px}
.foot-col li{font:400 15.5px/27px "Lato",sans-serif}
.foot-col p{margin-top:18px;font:400 15.5px/20.5px "Lato",sans-serif;width:260px}
.signup{left:843px;top:214px;width:254px;height:44px;border:1px solid #9a9a9a;border-radius:22px;font:400 14px/42px "Lato",sans-serif;padding-left:20px;color:#cfcfcf}
.copyright{left:0;top:370px;width:1200px;text-align:center;font:400 15px "Lato",sans-serif;color:#d6d6d6}
</style>
</head>
<body>

<div class="abs promo-strip">Free shipping on all orders $50 and over!</div>

<header class="abs site-nav">
  <div class="abs brand">Bright Nook</div>
  <nav class="abs nav-links">
    <a class="active" style="left:0">Home</a>
    <a style="left:78px">About</a>
    <a style="left:160px">Shop</a>
    <a style="left:233px">Product</a>
    <a style="left:324px">Blog</a>
    <a style="left:386px">Contact</a>
  </nav>
  <span class="abs social-ring" style="left:900px;top:28px"></span>
  <span class="abs social-ring" style="left:942px;top:28px"></span>
  <span class="abs social-ring" style="left:984px;top:28px"></span>
  <svg class="abs cart-icon" style="top:30px" width="44" height="34" viewBox="0 0 44 34" aria-label="Cart">
    <path d="M2 4h6l5 18h18l4-13H10" fill="none" stroke="#fff" stroke-width="2.5" stroke-linejoin="round"/>
    <path d="M12 13h22M14 18h19" stroke="#fff" stroke-width="1.5"/>
    <circle cx="15" cy="28" r="2.5" fill="#fff"/><circle cx="29" cy="28" r="2.5" fill="#fff"/>
    <circle cx="36" cy="8" r="7" fill="var(--teal)"/>
    <text x="36" y="11" font-size="9" font-family="Poppins,sans-serif" fill="#fff" text-anchor="middle">0</text>
  </svg>
</header>

<section class="abs hero">
  <div class="abs" role="img" aria-label="Lavender soaps, bath salt and oil bottles with dried lavender sprigs" style="left:420px;top:0;width:780px;height:581px;background:radial-gradient(ellipse at 45% 45%,#a78ad8 0%,#c6b4ea 35%,rgba(240,238,245,0) 70%)"></div>
  <h1 class="abs hero-title">Home<span>Wellness</span></h1>
  <p class="abs hero-copy">Sed ut perspiciatis unde omnis iste natus error sit voluptatem accusantium doloremque laudantium, totam rem aperiam, eaque ipsa quae</p>
  <a class="abs btn">Shop Now</a>
  <span class="abs slide-arrow" style="left:64px;top:256px"><svg width="36" height="36" viewBox="0 0 36 36"><path d="M20 11l-7 7 7 7" fill="none" stroke="#555" stroke-width="2"/></svg></span>
  <span class="abs slide-arrow" style="left:1096px;top:256px"><svg width="36" height="36" viewBox="0 0 36 36"><path d="M16 11l7 7-7 7" fill="none" stroke="#777" stroke-width="2"/></svg></span>
</section>

<section class="abs framed-banner sale-banner" role="img" aria-label="Lavender spa products under a purple tint">
  <div class="sale-title">50% OFF SALE GOING ON NOW!</div>
  <div class="sale-sub">BECAUSE SAVING MONEY ALSO MAKES US HAPPY</div>
  <a class="btn">Shop Now</a>
</section>

<div class="abs section-head" style="top:1094px">
  <h2>Featured Products</h2>
  <svg class="smile" width="82" height="22" viewBox="0 0 82 22"><path d="M4 4 Q41 30 78 4" fill="none" stroke="var(--teal)" stroke-width="7" stroke-linecap="round"/></svg>
  <p>The key to total bliss is nurturing the mind, body, and soul</p>
</div>

<div class="abs tile" role="img" aria-label="Spa tray with towel, candle and sponge" style="left:143px;top:1270px;width:241px;height:255px;background:linear-gradient(160deg,#ededed,#d4d2cf 60%,#8d8b88)"></div>
<div class="abs tile" role="img" aria-label="Woman relaxing with a towel wrap during a facial" style="left:389px;top:1270px;width:397px;height:511px;background:linear-gradient(180deg,#f1f0ec 0%,#d8b9a0 40%,#c49a7e 70%,#eeeeea 100%)"></div>
<div class="abs tile info-card" style="left:791px;top:1270px;width:266px;height:255px;background:var(--purple)">
  <h3>Nemo enim ipsam voluptas sit aspernatur</h3>
  <p>Lorem ipsum dolor sit amet conse ctetur adipisicing elit, sed do eiusmod tempor incididunt ut labore et dolore</p>
  <a class="more">LEARN MORE &nbsp;›</a>
</div>
<div class="abs tile" role="img" aria-label="White orchids with bath bottles" style="left:143px;top:1530px;width:241px;height:251px;background:linear-gradient(150deg,#f4f4f6,#dfe1e6 60%,#c9ccd3)"></div>
<div class="abs tile" role="img" aria-label="Natural soaps, lotions and jars with green leaves" style="left:791px;top:1530px;width:266px;height:251px;background:linear-gradient(160deg,#2f4a2a 0%,#7c8a5e 35%,#e4e1d8 65%,#f1efea)"></div>
<div class="abs tile" role="img" aria-label="Purple perfume bottles with lavender" style="left:143px;top:1785px;width:220px;height:236px;background:linear-gradient(150deg,#f6f5f7,#d9c6ea 55%,#a872c6)"></div>
<div class="abs tile info-card" style="left:368px;top:1785px;width:230px;height:236px;background:var(--teal);padding:38px 14px 0 24px">
  <h3>Nemo enim ipsam voluptas sit aspernatur</h3>
  <p style="margin-top:8px">Lorem ipsum dolor sit amet conse ctetur adipisicing elit, sed do eiusmod tempor incididunt ut labore et</p>
  <a class="more">LEARN MORE &nbsp;›</a>
</div>
<div class="abs tile" role="img" aria-label="Wooden bowls of lavender salt with spoons and soap" style="left:603px;top:1785px;width:454px;height:236px;background:linear-gradient(120deg,#f2f0f2,#c49a6f 35%,#8c63b8 55%,#c8a07a 75%,#efeaf0)"></div>

<section class="abs about">
  <h2 class="abs">ABOUT BRIGHT NOOK</h2>
  <svg class="abs smile" width="100" height="28" viewBox="0 0 100 28"><path d="M5 6 Q50 36 95 6" fill="none" stroke="var(--teal)" stroke-width="8" stroke-linecap="round"/></svg>
  <p class="abs">They say that home is where the heart is. But home is also where your mind and body reside. At Bright Nook we believe that home should be your place of Zen. A respite from the crazy world outside those walls. It is where you recharge your soul so you can approach each day with the focus and energy necessary to conquer the world.</p>
  <a class="abs btn">Tell Me More</a>
  <div class="abs" role="img" aria-label="Yellow and green gel bottles with handmade soaps and leaves" style="left:558px;top:63px;width:590px;height:406px;background:radial-gradient(ellipse at 45% 55%,#b9d43a 0%,#d6b93a 30%,rgba(236,238,241,0) 68%)"></div>
</section>

<section class="abs framed-banner pay-banner" role="img" aria-label="Lavender and bottles under a purple tint">
  <div class="pay-brand"><i></i>Ferrow</div>
  <div class="pay-line1">DON’T SWEAT IT.</div>
  <div class="pay-line2">YOU CAN PAY LATER</div>
</section>

<div class="abs section-head" style="top:2992px">
  <h2>The Happy Blog</h2>
  <svg class="smile" width="82" height="22" viewBox="0 0 82 22"><path d="M4 4 Q41 30 78 4" fill="none" stroke="var(--teal)" stroke-width="7" stroke-linecap="round"/></svg>
  <p>Food for the mind, tips for the body and exercises for the soul</p>
</div>

<span class="abs slide-arrow" style="left:74px;top:3333px;border-color:#666;width:36px;height:36px"><svg width="32" height="32" viewBox="0 0 32 32"><path d="M18 10l-6 6 6 6" fill="none" stroke="#555" stroke-width="2"/></svg></span>
<span class="abs slide-arrow" style="left:1090px;top:3333px;border-color:#666;width:36px;height:36px"><svg width="32" height="32" viewBox="0 0 32 32"><path d="M14 10l6 6-6 6" fill="none" stroke="#555" stroke-width="2"/></svg></span>

<article class="abs post" style="left:143px;top:3172px">
  <div class="thumb" role="img" aria-label="Olive oil bottles with lemons" style="background:linear-gradient(150deg,#e6d84a,#b88a1a 50%,#6a5a1a)"></div>
  <div class="body">
    <h3>Nemo ipsam voluptatem voluptas sit aspernatur</h3>
    <div class="date"><svg width="12" height="12" viewBox="0 0 12 12"><rect x="1" y="2" width="10" height="9" fill="none" stroke="currentColor" stroke-width="1.4"/><path d="M1 5h10" stroke="currentColor"/></svg>Oct 01, 2021</div>
    <p>Lorem ipsum dolor sit amet conse ctetur adipisicing elit, sed do eiusmod tempor incididunt ut</p>
    <a class="more">LEARN MORE &nbsp;›</a>
  </div>
</article>
<article class="abs post" style="left:459px;top:3172px">
  <div class="thumb" role="img" aria-label="Brushes, sponges and bottles among green leaves" style="background:linear-gradient(150deg,#1f3a22,#4c6b3c 45%,#cdb89a 75%,#2d4a2a)"></div>
  <div class="body">
    <h3>Nemo ipsam voluptatem voluptas sit aspernatur</h3>
    <div class="date"><svg width="12" height="12" viewBox="0 0 12 12"><rect x="1" y="2" width="10" height="9" fill="none" stroke="currentColor" stroke-width="1.4"/><path d="M1 5h10" stroke="currentColor"/></svg>Oct 01, 2021</div>
    <p>Lorem ipsum dolor sit amet conse ctetur adipisicing elit, sed do eiusmod tempor incididunt ut</p>
    <a class="more">LEARN MORE &nbsp;›</a>
  </div>
</article>
<article class="abs post" style="left:775px;top:3172px">
  <div class="thumb" role="img" aria-label="Hands holding a wellness gift box" style="background:linear-gradient(150deg,#e9e3d8,#c7a78a 45%,#8a6a4e 70%,#efe8df)"></div>
  <div class="body">
    <h3>Nemo ipsam voluptatem voluptas sit aspernatur</h3>
    <div class="date"><svg width="12" height="12" viewBox="0 0 12 12"><rect x="1" y="2" width="10" height="9" fill="none" stroke="currentColor" stroke-width="1.4"/><path d="M1 5h10" stroke="currentColor"/></svg>Oct 01, 2021</div>
    <p>Lorem ipsum dolor sit amet conse ctetur adipisicing elit, sed do eiusmod tempor incididunt ut</p>
    <a class="more">LEARN MORE &nbsp;›</a>
  </div>
</article>

<div class="abs chat-bubble">
  <svg width="50" height="46" viewBox="0 0 50 46"><rect x="2" y="2" width="46" height="34" rx="9" fill="#fff"/><path d="M12 34l-4 10 12-8z" fill="#fff"/><circle cx="15" cy="19" r="3.5" fill="var(--purple-deep)"/><circle cx="25" cy="19" r="3.5" fill="var(--purple-deep)"/><circle cx="35" cy="19" r="3.5" fill="var(--purple-deep)"/></svg>
</div>

<footer class="abs site-footer">
  <div class="abs brand">Bright Nook</div>
  <span class="abs foot-social" style="left:104px;top:132px"></span>
  <span class="abs foot-social" style="left:149px;top:132px"></span>
  <span class="abs foot-social" style="left:194px;top:132px"></span>
  <span class="abs foot-social" style="left:239px;top:132px"></span>

  <div class="abs foot-col" style="left:398px;top:64px">
    <h4>COMPANY</h4>
    <ul><li>Our Story</li><li>Careers</li><li>Privacy Policy</li><li>Terms and Conditions</li></ul>
  </div>
  <div class="abs foot-col" style="left:598px;top:64px">
    <h4>HELP</h4>
    <ul><li>Returns &amp; Exchanges</li><li>FAQ</li><li>help@YourBrightNook.com</li><li>Size Guide</li><li>Search</li></ul>
  </div>
  <div class="abs foot-col" style="left:843px;top:64px">
    <h4>SIGN UP FOR NEWSLETTER</h4>
    <p>Sed ut perspiciatis unde omnis iste natus voluptatem accusantium doloremque laudantium, totam rem aperiam, eaque ipsa quae ab</p>
  </div>
  <div class="abs signup">Enter email
    <svg class="abs" style="right:20px;top:15px" width="14" height="12" viewBox="0 0 14 12"><rect x="0" y="0" width="14" height="12" fill="#fff"/><path d="M0 0l7 6 7-6" fill="none" stroke="#1d1d1f" stroke-width="1.4"/></svg>
  </div>
  <div class="abs copyright">Copyright © 2021 Bright Nook. All Rights Reserved. Privacy Policy | Sitemap</div>
</footer>

</body>
</html>
```